Local Roofing/Construction company business needs new biz card design

We need a new business card design, current cards are from the start of this operation and generic at best. We are a local Construction Company (General Contractor) with a majority of our work originating from insurance claims-exterior finish work is the main focus (Roofs-Siding-Gutters etc). Heavily involved with homeowners and the low ball offers they receive from insurance company's after a insurable event takes place. I have attached some of our original logo file(s) below.

```html
<!DOCTYPE html>
<html lang="en">
<head>
<meta charset="utf-8">
<title>Oakhaven Builders – Business Card</title>
<link href="https://fonts.googleapis.com/css2?family=Open+Sans:wght@400;700;800&display=swap" rel="stylesheet">
<style>
  :root {
    --stage: #232323;
    --ink: #061c21;
    --green: #52bd6e;
    --paper: #f2f0ee;
    --white: #ffffff;
  }
  * { margin: 0; padding: 0; box-sizing: border-box; }
  html, body { width: 1200px; height: 780px; overflow: hidden; background: var(--stage); }
  body { position: relative; font-family: "Open Sans", Arial, sans-serif; }

  .card {
    position: absolute;
    width: 520px;
    height: 298px;
    overflow: hidden;
    top: 241px;
  }
  .card--front { left: 50px; background: var(--paper); }
  .card--back { left: 630px; background: var(--green); }

  .card__wave { position: absolute; inset: 0; width: 100%; height: 100%; }

  .brand {
    font-family: "Open Sans", Arial, sans-serif;
    font-weight: 800;
    text-transform: uppercase;
    letter-spacing: 0.04em;
    display: flex;
    align-items: center;
    gap: 10px;
    white-space: nowrap;
  }
  .brand__square { display: block; background: currentColor; flex: none; }

  .card--front .brand--small {
    position: absolute; top: 22px; left: 22px;
    color: var(--ink); font-size: 18px;
  }
  .card--front .brand--small .brand__square { width: 13px; height: 13px; }

  .card--front .brand--large {
    position: absolute; left: 330px; top: 124px;
    width: 170px;
    color: var(--white); font-size: 19px; line-height: 1.3;
    flex-direction: column; gap: 12px; text-align: center;
  }
  .brand--large .brand__square { width: 34px; height: 34px; }

  .holder {
    position: absolute; left: 22px; top: 70px;
    border-left: 6px solid var(--green);
    padding-left: 10px;
  }
  .holder__name { font-size: 21px; font-weight: 700; color: var(--ink); line-height: 1.1; }
  .holder__first { color: var(--green); }
  .holder__role { font-size: 12px; color: var(--ink); margin-top: 2px; }

  .contact {
    position: absolute; left: 22px; top: 134px;
    list-style: none; font-size: 12px; color: var(--ink); line-height: 1.55;
  }
  .contact__address { margin-left: 22px; margin-bottom: 4px; }
  .contact__item { display: flex; align-items: center; gap: 8px; }
  .contact__icon { width: 14px; height: 14px; fill: none; stroke: var(--green); stroke-width: 2; flex: none; }

  .card--back .brand--main {
    position: absolute; left: 50%; top: 50%;
    transform: translate(-50%, -50%);
    color: var(--ink); font-size: 34px; gap: 16px;
  }
  .brand--main .brand__square { width: 30px; height: 30px; }
</style>
</head>
<body>
  <section class="card card--front" aria-label="Business card front">
    <svg class="card__wave" viewBox="0 0 520 298" preserveAspectRatio="none" aria-hidden="true">
      <path d="M380 0 C 360 80, 290 120, 270 190 C 258 240, 240 275, 232 298 L 250 298 C 262 272, 280 236, 292 190 C 318 125, 380 80, 396 0 Z" fill="var(--green)"/>
      <path d="M392 0 C 376 82, 310 128, 294 190 C 282 236, 264 272, 256 298 L 520 298 L 520 0 Z" fill="var(--ink)"/>
    </svg>

    <div class="brand brand--small"><span class="brand__square"></span>Oakhaven Builders</div>

    <div class="holder">
      <p class="holder__name"><span class="holder__first">Marta</span> Velinska</p>
      <p class="holder__role">Co-Founder</p>
    </div>

    <ul class="contact">
      <li class="contact__address">42 Copper Field Ln<br>Brookton, MO 63000</li>
      <li class="contact__item">
        <svg class="contact__icon" viewBox="0 0 16 16" aria-hidden="true"><path d="M3 2h3l1.5 3.5-2 1.2a8 8 0 0 0 3.8 3.8l1.2-2L14 10v3a1 1 0 0 1-1 1A11 11 0 0 1 2 3a1 1 0 0 1 1-1z"/></svg>
        555-201-0142
      </li>
      <li class="contact__item">
        <svg class="contact__icon" viewBox="0 0 16 16" aria-hidden="true"><path d="M3 2h3l1.5 3.5-2 1.2a8 8 0 0 0 3.8 3.8l1.2-2L14 10v3a1 1 0 0 1-1 1A11 11 0 0 1 2 3a1 1 0 0 1 1-1z"/></svg>
        555-201-0178 (Emergency)
      </li>
      <li class="contact__item">
        <svg class="contact__icon" viewBox="0 0 16 16" aria-hidden="true"><circle cx="8" cy="8" r="6"/><path d="M2 8h12M8 2c2.5 3 2.5 9 0 12M8 2c-2.5 3-2.5 9 0 12"/></svg>
        www.oakhavenbuilders.com
      </li>
      <li class="contact__item">
        <svg class="contact__icon" viewBox="0 0 16 16" aria-hidden="true"><rect x="2" y="4" width="12" height="9" rx="1"/><path d="M2 5l6 4 6-4"/></svg>
        office@oakhavenbuilders.com
      </li>
    </ul>

    <div class="brand brand--large"><span class="brand__square"></span><span>Oakhaven<br>Builders</span></div>
  </section>

  <section class="card card--back" aria-label="Business card back">
    <div class="brand brand--main"><span class="brand__square"></span>Oakhaven Builders</div>
  </section>
</body>
</html>
```